Business Cards Needed for Innovative Healthcare Marketing Company

We are a marketing company focused on healthcare. Our company is all about rebranding yourself renewing your image and generating results. The phoenix stands for "reborn" or "rising" which we provide new brands for our clients we take their old brands and renew it with creativity and innovation. I am looking for a business card with color dimension. I have attached an example of a card I think has the look and feel of what I am trying to accomplish. I like that the card example has black and grey font colors, I like the font placement and the small logo, I really like the use of the colors on the right those are the colors of my logo. My logo is phoenix so maybe incorporating flames similar to that design. I would like the back a solid color maybe red with an opaque version of the logo and website. As a marketing company I am always open to creative liberty!

Target Market(s)

Doctors and business professionals.

Industry/Entity Type

Marketing

Contact Information for Business Card

Valcorne Health Care Marketing
Marla Tenwick- CEO
#(512)638-2974
email-marla@valcorne.com
website- valcorne.com

Font styles to use
Sans Serif

Colors
ec1f27
f37122
ffc214
fbed22
fbf289
f04a50

Requirements
Must have
• The logo and required information
Nice to have
• icons by the information
Should not have
• child like font

```html
<!DOCTYPE html>
<html lang="en">
<head>
<meta charset="utf-8">
<title>Valcorne Health Care Marketing – Business Card</title>
<link rel="stylesheet" href="https://fonts.googleapis.com/css2?family=Open+Sans:wght@300;400;700&display=swap">
<style>
  :root {
    --backdrop: #3b3b3b;
    --card-white: #ffffff;
    --deep-red: #9e1d22;
    --brand-red: #c42026;
    --flame-orange: #f37122;
    --amber: #f7941d;
    --text-grey: #5a5a5a;
    --rule-red: #b3262b;
  }
  * { box-sizing: border-box; margin: 0; padding: 0; }
  html, body {
    width: 1200px; height: 950px; overflow: hidden;
    background: var(--backdrop);
    font-family: "Open Sans", Arial, sans-serif;
  }
  .canvas {
    width: 1200px; height: 950px;
    display: flex; flex-direction: column; align-items: center; justify-content: center;
    gap: 60px;
  }
  .card {
    position: relative;
    width: 700px; height: 400px;
    border-radius: 22px;
    overflow: hidden;
    box-shadow: 0 12px 30px rgba(0,0,0,0.45);
  }

  /* Front */
  .card-front { background: var(--card-white); }
  .top-band {
    position: absolute; left: 0; top: 0; width: 100%; height: 16px;
    background: linear-gradient(90deg, var(--deep-red) 0%, var(--brand-red) 62%, var(--flame-orange) 63%, var(--amber) 70%, var(--brand-red) 71%, var(--deep-red) 100%);
  }
  .name-block {
    position: absolute; right: 48px; top: 54px; text-align: right;
  }
  .person-name {
    font-weight: 700; font-size: 30px; color: var(--deep-red); letter-spacing: 0.2px;
  }
  .person-title {
    font-weight: 400; font-size: 17px; color: var(--flame-orange); margin-top: 2px;
  }
  .name-rule {
    position: absolute; left: 250px; right: 48px; top: 102px;
    height: 2px; background: var(--rule-red);
  }
  .brand-lockup {
    position: absolute; left: 48px; top: 150px;
    display: flex; align-items: center; gap: 18px;
    color: var(--deep-red); font-weight: 300;
  }
  .brand-dot {
    width: 64px; height: 64px; border-radius: 50%;
    background: var(--brand-red);
    flex: none;
  }
  .brand-name { font-size: 56px; line-height: 1; letter-spacing: 3px; text-transform: uppercase; }
  .brand-tagline { font-size: 14px; letter-spacing: 2.6px; text-transform: uppercase; margin-top: 6px; }

  .contact-list {
    position: absolute; left: 300px; top: 262px;
    display: grid; grid-template-columns: auto 2px auto; column-gap: 12px; row-gap: 6px;
    font-size: 16px; align-items: center;
  }
  .contact-label { color: var(--brand-red); text-align: right; }
  .contact-divider { width: 2px; height: 18px; background: #9a9a9a; }
  .contact-value { color: var(--text-grey); }

  /* Back */
  .card-back {
    background: radial-gradient(ellipse at 45% 40%, var(--amber) 0%, var(--flame-orange) 38%, var(--brand-red) 80%, var(--deep-red) 100%);
    display: flex; align-items: center; justify-content: center;
  }
  .back-lockup {
    display: flex; flex-direction: column; align-items: center;
    color: #ffffff; font-weight: 300;
  }
  .back-lockup .brand-dot { background: #ffffff; opacity: 0.9; width: 80px; height: 80px; margin-bottom: 22px; }
  .back-lockup .brand-name { font-size: 68px; letter-spacing: 5px; }
  .back-lockup .brand-tagline { font-size: 17px; letter-spacing: 3.5px; margin-top: 8px; padding-bottom: 8px; border-bottom: 1px solid rgba(255,255,255,0.8); }
</style>
</head>
<body>
<main class="canvas">
  <section class="card card-front" aria-label="Business card front">
    <div class="top-band"></div>
    <div class="name-block">
      <p class="person-name">Marla Tenwick</p>
      <p class="person-title">CEO</p>
    </div>
    <div class="name-rule"></div>
    <div class="brand-lockup">
      <span class="brand-dot"></span>
      <div>
        <p class="brand-name">Valcorne</p>
        <p class="brand-tagline">Health Care Marketing</p>
      </div>
    </div>
    <div class="contact-list">
      <span class="contact-label">Tel</span><span class="contact-divider"></span><span class="contact-value">(512)638-2974</span>
      <span class="contact-label">Email</span><span class="contact-divider"></span><span class="contact-value">marla@valcorne.com</span>
      <span class="contact-label">Web</span><span class="contact-divider"></span><span class="contact-value">www.valcorne.com</span>
    </div>
  </section>

  <section class="card card-back" aria-label="Business card back">
    <div class="back-lockup">
      <span class="brand-dot"></span>
      <p class="brand-name">Valcorne</p>
      <p class="brand-tagline">Health Care Marketing</p>
    </div>
  </section>
</main>
</body>
</html>
```